Looking for a dynamic business card for a pizzeria.

A business card with our food, logo, and space for name, title, email, website, phone. The card should convey quality, unique, amazing. On the front, I envision food photo or photos with the owners names and contact information. On the back, more food with locations, website, facebook, twitter, instagram icons. It should look polished, not cartoonish, or plain.
Target Market(s)
upscale, local food buyers, 30-50 years in age.
Industry/Entity Type
Restaurant
Contact Information for Business Card
Business Name: Bru'nettix, LLC
Website: www.brunettix.com
Back:
2 locations: (can list on the back of card)
1. Harborside
4087 Corlan Avenue
Larkport, OR 97412
360-481-5067
2. Cedar Knoll
7315 Wendmere Road
Larkport, OR 97418
360-293-8840
front:
EDITABLE space for
Business name
Person's Name
title
2nd title
Email address
cell-phone number
Requirements
Must have
- logo
- my food photo or photos (no watermarks showing)
- locations on back
- Person contact information on front
- full bleed

```html
<!DOCTYPE html>
<html lang="en">
<head>
<meta charset="utf-8">
<title>Bru'nettix Business Card</title>
<link rel="stylesheet" href="https://fonts.googleapis.com/css2?family=Arimo:wght@400;700&display=swap">
<style>
  :root {
    --page: #e9e6e1;
    --paper: #ffffff;
    --basil: #2e5a34;
    --tomato: #c0161a;
    --tomato-dark: #7f0e10;
    --ink-light: #ffffff;
    --shadow: rgba(40, 30, 20, 0.25);
  }
  html, body {
    margin: 0;
    padding: 0;
    overflow: hidden;
  }
  body {
    width: 1200px;
    height: 950px;
    background: var(--page);
    font-family: "Arimo", Arial, sans-serif;
    position: relative;
  }
  .card {
    position: absolute;
    left: 250px;
    width: 700px;
    height: 400px;
    overflow: hidden;
    box-shadow: 0 8px 24px var(--shadow);
  }
  .card--back {
    top: 50px;
    background: linear-gradient(120deg, var(--tomato) 0%, #a81216 55%, var(--tomato-dark) 100%);
  }
  .card--front {
    top: 500px;
    background: var(--paper);
  }

  /* Back */
  .social {
    position: absolute;
    top: 26px;
    right: 30px;
    display: flex;
    gap: 12px;
  }
  .social__dot {
    width: 16px;
    height: 16px;
    border-radius: 50%;
    background: rgba(255, 255, 255, 0.8);
  }
  .back-brand {
    position: absolute;
    top: 150px;
    left: 0;
    right: 0;
    display: flex;
    justify-content: center;
    align-items: center;
    gap: 16px;
  }
  .back-brand__name {
    font-size: 54px;
    font-weight: 700;
    color: var(--ink-light);
    letter-spacing: 1px;
  }
  .back-brand__mark {
    width: 64px;
    height: 64px;
    border-radius: 50%;
    background: rgba(255, 255, 255, 0.85);
  }
  .back-web {
    position: absolute;
    top: 250px;
    left: 0;
    right: 0;
    margin: 0;
    text-align: center;
    color: rgba(255, 255, 255, 0.85);
    font-size: 17px;
    letter-spacing: 6px;
  }

  /* Front */
  .wave {
    position: absolute;
    inset: 0;
  }
  .brand {
    position: absolute;
    top: 48px;
    left: 40px;
    display: flex;
    align-items: center;
    gap: 12px;
  }
  .brand__name {
    font-size: 42px;
    font-weight: 700;
    color: var(--basil);
    letter-spacing: 0.5px;
  }
  .brand__mark {
    width: 56px;
    height: 56px;
    border-radius: 50%;
    background: var(--tomato);
  }
  .person {
    position: absolute;
    top: 128px;
    left: 110px;
    text-align: center;
  }
  .person__name {
    margin: 0;
    font-size: 20px;
    font-weight: 700;
    color: var(--basil);
    letter-spacing: 0.5px;
  }
  .person__title {
    margin: 2px 0 0;
    font-size: 15px;
    color: var(--tomato);
  }
  .contact {
    position: absolute;
    right: 26px;
    top: 150px;
    text-align: right;
    color: var(--ink-light);
    font-size: 15px;
    line-height: 17px;
  }
  .location {
    margin: 0 0 4px;
  }
  .location p, .direct p {
    margin: 0;
  }
  .direct {
    margin-top: 12px;
  }
  .direct__row {
    display: flex;
    justify-content: flex-end;
    align-items: center;
    gap: 10px;
    height: 24px;
  }
  .direct__icon {
    width: 16px;
    height: 16px;
    fill: var(--ink-light);
  }
</style>
</head>
<body>

  <section class="card card--back" aria-label="Card back">
    <div class="social" aria-label="Social links">
      <span class="social__dot"></span>
      <span class="social__dot"></span>
    </div>
    <div class="back-brand">
      <span class="back-brand__name">BRU'NETTIX</span>
      <span class="back-brand__mark"></span>
    </div>
    <p class="back-web">www.brunettix.com</p>
  </section>

  <section class="card card--front" aria-label="Card front">
    <svg class="wave" viewBox="0 0 700 400" preserveAspectRatio="none" aria-hidden="true">
      <path d="M0,196 C180,266 360,226 700,8 L700,24 C360,242 180,282 0,212 Z" fill="var(--tomato)"/>
      <path d="M0,220 C180,290 360,250 700,32 L700,400 L0,400 Z" fill="var(--basil)"/>
    </svg>

    <div class="brand">
      <span class="brand__name">BRU'NETTIX</span>
      <span class="brand__mark"></span>
    </div>

    <div class="person">
      <p class="person__name">MARCO LENTI</p>
      <p class="person__title">President</p>
    </div>

    <div class="contact">
      <div class="location">
        <p>Harborside</p>
        <p>4087 Corlan Avenue</p>
        <p>Larkport, OR 97412</p>
        <p>Phone:360-481-5067</p>
      </div>
      <div class="location">
        <p>Cedar Knoll</p>
        <p>7315 Wendmere Road</p>
        <p>Larkport, OR 97418</p>
        <p>Phone:360-293-8840</p>
      </div>
      <div class="direct">
        <div class="direct__row">
          <p>689 512 3074</p>
          <svg class="direct__icon" viewBox="0 0 16 16" aria-hidden="true"><path d="M4 0h8a1 1 0 0 1 1 1v14a1 1 0 0 1-1 1H4a1 1 0 0 1-1-1V1a1 1 0 0 1 1-1zm1 2v10h6V2zm3 11a1 1 0 1 0 0 2 1 1 0 0 0 0-2z"/></svg>
        </div>
        <div class="direct__row">
          <p>name@brunettix.com</p>
          <svg class="direct__icon" viewBox="0 0 16 16" aria-hidden="true"><path d="M0 3h16v10H0zm1.5 1.2L8 9l6.5-4.8V4h-13z"/></svg>
        </div>
        <div class="direct__row">
          <p>www.brunettix.com</p>
          <svg class="direct__icon" viewBox="0 0 16 16" aria-hidden="true"><circle cx="8" cy="8" r="7.5"/><path d="M1 8h14M8 1c3 3 3 11 0 14M8 1c-3 3-3 11 0 14" stroke="var(--basil)" stroke-width="1" fill="none"/></svg>
        </div>
      </div>
    </div>
  </section>

</body>
</html>
```